Clothing for elderly and disabled persons business card

I have seen a design on the Orlo website with a partial hand holding a heart I would like that to be incorporated above the i in Tulip
The colours should be either soft green and pinks.
The final design should communicate care, love, easy fit comfort clothing for the frail and disabled.

Tulip
Gentle WearGarments

Target Market(s)

Nursing Homes, Elderly in care or just anyone with limited mobility

Industry/Entity Type

Clothing

Contact Information for Business Card

Tulip Gentle Wear Garments
Maree Coltart Owner Sales Consultant
Phone 0452 786 041 Fax 08 9627 3058
Email: tulipgentlegarments@mailbox.example
Website: ?????? to be created

Requirements
Nice to have
• A hand holding a heart this must form part of the i in Tulip, instead of the dot above the i I want the hand holding the heart.

```html
<!DOCTYPE html>
<html lang="en">
<head>
<meta charset="utf-8">
<title>Tulip Gentle Wear Garments – Business Cards</title>
<link rel="stylesheet" href="https://fonts.googleapis.com/css2?family=Libre+Baskerville&family=Open+Sans:wght@400;700&display=swap">
<style>
  :root {
    --board: #d1d2d4;
    --card: #ffffff;
    --brand-green: #2f9a4a;
    --deep-green: #1f7a35;
    --light-green: #8cc63f;
    --petal-pink: #d98a9c;
    --ink-grey: #8a8b8d;
    --label: #111111;
    --crop: #9a9a9a;
  }
  * { box-sizing: border-box; margin: 0; padding: 0; }
  html, body { width: 688px; height: 1200px; overflow: hidden; }
  body {
    background: var(--board);
    font-family: "Open Sans", Arial, sans-serif;
    position: relative;
  }
  .column-label {
    position: absolute;
    top: 352px;
    width: 300px;
    text-align: center;
    font-size: 17px;
    letter-spacing: 0.5px;
    color: var(--label);
  }
  .column-label--front { left: 28px; }
  .column-label--back { left: 360px; }

  .card {
    position: absolute;
    width: 300px;
    height: 171px;
    background: var(--card);
  }
  .card--front-1 { left: 28px; top: 400px; }
  .card--back-1 { left: 360px; top: 400px; }
  .card--front-2 { left: 28px; top: 611px; }
  .card--back-2 { left: 360px; top: 611px; }

  .card--green {
    background: radial-gradient(ellipse 60% 70% at 45% 45%, var(--light-green) 0%, #4fa53c 45%, var(--deep-green) 100%);
  }

  .crop-marks { position: absolute; inset: -6px; pointer-events: none; }
  .crop-marks span {
    position: absolute;
    width: 9px; height: 9px;
    border: 1px solid var(--crop);
  }
  .crop-marks .tl { left: 0; top: 0; border-width: 0 1px 1px 0; }
  .crop-marks .tr { right: 0; top: 0; border-width: 0 0 1px 1px; }
  .crop-marks .bl { left: 0; bottom: 0; border-width: 1px 1px 0 0; }
  .crop-marks .br { right: 0; bottom: 0; border-width: 1px 0 0 1px; }

  .brand {
    position: absolute;
    display: flex;
    align-items: center;
    gap: 6px;
    font-family: "Libre Baskerville", Georgia, serif;
    font-size: 15px;
    color: var(--brand-green);
    white-space: nowrap;
  }
  .brand__dot {
    width: 9px; height: 9px;
    border-radius: 50%;
    background: var(--petal-pink);
  }
  .card--front-1 .brand, .card--front-2 .brand { left: 34px; top: 42px; }
  .card--back-1 .brand, .card--back-2 .brand { left: 38px; top: 78px; }
  .card--green .brand { color: #ffffff; }

  .contact {
    position: absolute;
    left: 174px;
    top: 76px;
    color: var(--ink-grey);
    font-size: 8.5px;
    line-height: 1.3;
  }
  .contact__name { font-weight: 700; font-size: 10px; }
  .contact__role { font-size: 6.5px; }

  .online {
    position: absolute;
    left: 0; right: 0;
    top: 126px;
    text-align: center;
    color: var(--ink-grey);
    font-size: 8.5px;
    line-height: 1.3;
  }
</style>
</head>
<body>
  <div class="column-label column-label--front">FRONT</div>
  <div class="column-label column-label--back">BACK</div>

  <section class="card card--front-1">
    <div class="crop-marks"><span class="tl"></span><span class="tr"></span><span class="bl"></span><span class="br"></span></div>
    <div class="brand"><span class="brand__dot"></span>Tulip Gentle Wear Garments</div>
    <div class="contact">
      <p class="contact__name">Jolene Ashworth</p>
      <p class="contact__role">Owner/Sales Consultant</p>
      <p>Phone 0419 532 807</p>
      <p>Fax 08 9627 3058</p>
    </div>
    <div class="online">
      <p>Email tulipgentlegarments@mailbox.example</p>
      <p>Website Lorem@Ipsumdolor</p>
    </div>
  </section>

  <section class="card card--back-1 card--green">
    <div class="crop-marks"><span class="tl"></span><span class="tr"></span><span class="bl"></span><span class="br"></span></div>
    <div class="brand"><span class="brand__dot"></span>Tulip Gentle Wear Garments</div>
  </section>

  <section class="card card--front-2">
    <div class="crop-marks"><span class="tl"></span><span class="tr"></span><span class="bl"></span><span class="br"></span></div>
    <div class="brand"><span class="brand__dot"></span>Tulip Gentle Wear Garments</div>
    <div class="contact">
      <p class="contact__name">Maree Coltart</p>
      <p class="contact__role">Owner/Sales Consultant</p>
      <p>Phone 0452 786 041</p>
      <p>Fax 08 9627 3058</p>
    </div>
    <div class="online">
      <p>Email tulipgentlegarments@mailbox.example</p>
      <p>Website Lorem@Ipsumdolor</p>
    </div>
  </section>

  <section class="card card--back-2">
    <div class="crop-marks"><span class="tl"></span><span class="tr"></span><span class="bl"></span><span class="br"></span></div>
    <div class="brand"><span class="brand__dot"></span>Tulip Gentle Wear Garments</div>
  </section>
</body>
</html>
```